Aunt Wilma's Ember-Kissed Husk Shack Concession Trailer Logo Wraps

Looking to put my design concept into a final production-ready format for vinyl-based logo "wrap" on the exterior of a 7x12 black concession trailer selling farm-fresh corn on the cob slathered in flavor flamboyance, corn in a cup, corn over crushed snacks (Crunvels, Zaplins, Puffnars, etc.) served in the bags, fire-roasted street corn (Mexican elotes), corn grits, corn chowder, cornbread, corndogs. I have my fonts and colors and a flame graphic I've roughly edited/reworked attempting to make it work and need a design pro to bring it all together for me. The approximate size of the graphics on the four sides of the trailer will be: the serving window when closed (48"L x 24"H); front (48"x48"); full right side (11'x5'); door (6'x2') and possibly the left side next to door (3'x5'). Pictures uploaded.
Target Market(s)
Food truck festivals, private catering gigs, fairs, farm markets, concerts, etc.
Font styles to use
Other font styles liked:
- flame fetish, Algerian
Requirements
Must have
- My color scheme as depicted in uploaded files, flame fetish font uploaded (will consider similar fonts), flame/fire artwork, bright bold colors that pop against a black background
Nice to have
- straight line of flames on each side of the "fire-roasted" text, flowing from the first and last letter

```html
<!DOCTYPE html>
<html lang="en">
<head>
<meta charset="utf-8">
<title>Aunt Wilma's Ember-Kissed Husk Shack – Trailer Wrap</title>
<link rel="stylesheet" href="https://fonts.googleapis.com/css2?family=Almendra+SC&display=swap">
<style>
  :root {
    --night: #060606;
    --corn-yellow: #f3e81c;
    --tagline-blue: #a9d4ff;
    --ember: #ff7a12;
    --ember-deep: #d1340a;
  }
  * { margin: 0; padding: 0; box-sizing: border-box; }
  html, body { width: 1200px; height: 571px; overflow: hidden; background: var(--night); }

  .wrap-panel {
    position: relative;
    width: 1200px;
    height: 571px;
    background: var(--night);
    overflow: hidden;
    font-family: "Almendra SC", serif;
  }

  .menu-line {
    position: absolute;
    top: 14px;
    left: 0;
    width: 100%;
    text-align: center;
    font-size: 25px;
    letter-spacing: 1px;
    color: var(--corn-yellow);
    white-space: nowrap;
  }
  .menu-line .divider { margin: 0 14px; }

  .flame-strip {
    position: absolute;
    left: 0;
    top: 200px;
    width: 1200px;
    height: 123px;
    background:
      radial-gradient(ellipse 90px 120px at 0% 100%, rgba(255,170,40,.95), rgba(255,90,10,.6) 50%, transparent 80%),
      radial-gradient(ellipse 90px 120px at 100% 100%, rgba(255,170,40,.95), rgba(255,90,10,.6) 50%, transparent 80%),
      linear-gradient(to top, rgba(255,110,20,.85) 0%, rgba(209,52,10,.45) 30%, transparent 70%);
  }
  .flame-reflection {
    position: absolute;
    left: 0;
    top: 323px;
    width: 1200px;
    height: 90px;
    background: linear-gradient(to bottom, rgba(120,60,20,.35), rgba(40,30,20,.15) 50%, transparent);
  }

  .brand-block {
    position: absolute;
    top: 0;
    left: 0;
    width: 100%;
    height: 100%;
    color: var(--corn-yellow);
    font-weight: 400;
    text-align: center;
    white-space: nowrap;
  }
  .brand-block span {
    position: absolute;
    left: 0;
    width: 100%;
    line-height: 1;
    display: block;
  }
  .brand-first  { top: 82px;  font-size: 96px; }
  .brand-middle { top: 246px; font-size: 66px; }
  .brand-last   { top: 350px; font-size: 124px; letter-spacing: 2px; }

  .tagline {
    position: absolute;
    top: 506px;
    left: 0;
    width: 100%;
    text-align: center;
    font-size: 34px;
    line-height: 1;
    color: var(--tagline-blue);
    white-space: nowrap;
  }
</style>
</head>
<body>
  <main class="wrap-panel">
    <p class="menu-line">ELOTES<span class="divider">|</span>CORN IN A CUP<span class="divider">|</span>CORN GRITS<span class="divider">|</span>CORN CHOWDER<span class="divider">|</span>CORNBREAD<span class="divider">|</span>CORNDOGS</p>

    <div class="flame-strip" role="img" aria-label="Straight line of fire flames running across the panel"></div>
    <div class="flame-reflection" role="img" aria-label="Soft reflection of the flames below the fire line"></div>

    <h1 class="brand-block">
      <span class="brand-first">Aunt Wilma's</span>
      <span class="brand-middle">Ember-Kissed</span>
      <span class="brand-last">Husk Shack</span>
    </h1>

    <p class="tagline">Sweet cobs dripping with bold, blazing seasoning flair!</p>
  </main>
</body>
</html>
```